Home Staging Company needs business card design

We're a home staging company called Brightly Settled Home Staging. We would like a business card design that includes aqua and gray. Our current logo of house within chair is fine but I find we almost always use the logo in one color. I'll upload images of front and back of our current card and our logo. Note that we have dropped "Solutions" from our company name and don't want to include it on the card.

Target Market(s)

Realtors and homeowners - people interested in selling their homes

Contact Information for Business Card

Marisol Thistlewood
Brightly Settled Home Staging
757-555-0193
www.brightlysettled.com
marisol@brightlysettled.com

Font styles to use
Serif
Script

Requirements
Must have
• My logo and contact details
• UPDATE***
• I forgot to say that the company name should be included on the front of the card somehow.

```html
<!DOCTYPE html>
<html lang="en">
<head>
<meta charset="utf-8">
<title>Brightly Settled Home Staging – Business Card</title>
<link rel="stylesheet" href="https://fonts.googleapis.com/css2?family=Playfair+Display:wght@400&family=Roboto:wght@400&family=Roboto+Condensed:wght@400&family=Quicksand:wght@500&display=swap">
<style>
  :root {
    --page-bg: #c3c3c3;
    --card-dark: #3a3d41;
    --card-light-top: #f4f4f4;
    --card-light-bottom: #e6e6e6;
    --aqua: #4aabb8;
    --charcoal: #2f3133;
    --ink: #3a3a3a;
    --muted: #4a4a4a;
    --soft-white: #ececec;
  }
  * { box-sizing: border-box; margin: 0; padding: 0; }
  html, body {
    width: 1200px; height: 576px; overflow: hidden;
    background: var(--page-bg);
  }
  .canvas { position: relative; width: 1200px; height: 576px; }
  .card {
    position: absolute; top: 140px;
    width: 484px; height: 292px;
    border-radius: 14px;
    box-shadow: 0 3px 6px rgba(0,0,0,0.22);
    overflow: hidden;
  }
  /* Front */
  .card-front { left: 82px; background: var(--card-dark); }
  .front-name {
    position: absolute; left: 0; right: 0; top: 110px;
    text-align: center;
    font-family: "Playfair Display", serif; font-weight: 400;
    color: var(--soft-white);
  }
  .front-name .line-main { display: block; font-size: 40px; line-height: 1; }
  .front-name .line-sub {
    display: block; margin-top: 10px;
    font-size: 16px; letter-spacing: 0.42em; text-transform: uppercase;
  }
  .front-url {
    position: absolute; left: 0; right: 0; top: 266px;
    text-align: center;
    font-family: "Quicksand", sans-serif; font-weight: 500; font-size: 13px;
    color: var(--aqua);
  }
  /* Back */
  .card-back {
    left: 602px;
    background: linear-gradient(180deg, var(--card-light-top), var(--card-light-bottom));
  }
  .brand {
    position: absolute; left: 22px; top: 42px;
    display: flex; align-items: center; gap: 12px;
  }
  .brand-dot { width: 44px; height: 44px; border-radius: 50%; background: var(--aqua); }
  .brand-name {
    font-family: "Playfair Display", serif; font-weight: 400;
    font-size: 19px; line-height: 1.15; color: var(--charcoal);
  }
  .person { position: absolute; left: 23px; top: 148px; }
  .person-name {
    font-family: "Roboto Condensed", sans-serif; font-size: 20px; color: var(--ink);
  }
  .person-name .surname { color: var(--aqua); }
  .person-title {
    margin-top: 4px;
    font-family: "Roboto", sans-serif; font-size: 11px; color: var(--muted);
  }
  .contacts {
    position: absolute; left: 28px; top: 220px; list-style: none;
    font-family: "Roboto", sans-serif; font-size: 12px; color: var(--ink);
  }
  .contacts li { display: flex; align-items: center; gap: 8px; height: 17px; }
  .contacts svg { width: 10px; height: 10px; fill: var(--aqua); flex: none; }
</style>
</head>
<body>
<main class="canvas">
  <section class="card card-front" aria-label="Card front">
    <h1 class="front-name">
      <span class="line-main">Brightly Settled</span>
      <span class="line-sub">Home Staging</span>
    </h1>
    <p class="front-url">www.brightlysettled.com</p>
  </section>

  <section class="card card-back" aria-label="Card back">
    <div class="brand">
      <span class="brand-dot"></span>
      <span class="brand-name">Brightly Settled<br>Home Staging</span>
    </div>
    <div class="person">
      <p class="person-name">Marisol <span class="surname">Thistlewood</span></p>
      <p class="person-title">Managing Director</p>
    </div>
    <ul class="contacts">
      <li>
        <svg viewBox="0 0 10 10" aria-hidden="true"><path d="M1 3.2C1 2 2.5 1.2 5 1.2S9 2 9 3.2V4H7V3.2H3V4H1z M2.5 4.6h5L9 8.8H1z"/></svg>
        757-555-0193
      </li>
      <li>
        <svg viewBox="0 0 10 10" aria-hidden="true"><path d="M5 .5a4.5 4.5 0 1 0 0 9 4.5 4.5 0 0 0 0-9zm0 1c.6.6 1 1.6 1.1 3H3.9C4 3.1 4.4 2.1 5 1.5zM1.6 4.5a3.5 3.5 0 0 1 1.6-2.4c-.3.7-.4 1.5-.4 2.4zm0 1h1.2c0 .9.2 1.7.4 2.4a3.5 3.5 0 0 1-1.6-2.4zm3.4 3c-.6-.6-1-1.6-1.1-3h2.2c-.1 1.4-.5 2.4-1.1 3zm1.8-.6c.3-.7.4-1.5.4-2.4h1.2a3.5 3.5 0 0 1-1.6 2.4zm.4-3.4c0-.9-.2-1.7-.4-2.4a3.5 3.5 0 0 1 1.6 2.4z"/></svg>
        www.brightlysettled.com
      </li>
      <li>
        <svg viewBox="0 0 10 10" aria-hidden="true"><path d="M.5 2h9v6h-9z M1 2.4 5 5.6 9 2.4" stroke="#e9e9e9" stroke-width=".7"/></svg>
        marisol@brightlysettled.com
      </li>
    </ul>
  </section>
</main>
</body>
</html>
```